Business Cards Design for the electrical wholesaler: clean bold dynamic :)

We need a business card design that would follow our latest brand guidelines. As an electrical wholesaler we want to bring a fresh look and feel into the industry. The design should be clean bold and dynamic. It should come alive with the renewed energy of our green colour. Our grey colour should keep things balanced and complement the notion of maturity and responsibility. We employ Lato as a corporate font however are not bound by this font and we’re open to interpretation here.

Target Market(s)

Electrical contractors

Industry/Entity Type

Business

Contact Information for Business Card

Logo
Name & Surname: Halyna Dorosh
Job Title: Director of Marketing
Email: halya.dorosh@quillmail.example
Cell phone: 780.555.0127
Address: 20517 - 87 Ave. Edmonton, AB, Canada. T6K 4N8
Business Phone: 780.555.0184
Website: www.brovix.example

Font styles to use
Other font styles liked:
• Lato

Requirements
Must have
• Logo & website
Nice to have
• Brand elements - some of them you may find in the attached Brand Guidelines (e.g. three lines on the background signifying "W")

```html
<!DOCTYPE html>
<html lang="en">
<head>
<meta charset="utf-8">
<title>Brovix business card</title>
<link rel="stylesheet" href="https://fonts.googleapis.com/css2?family=Work+Sans:wght@400;500;600&display=swap">
<style>
  :root {
    --backdrop: #141414;
    --card: #262626;
    --card-edge: #2e2e2e;
    --green: #8cc63f;
    --white: #f4f4f4;
  }
  * { box-sizing: border-box; margin: 0; padding: 0; }
  html, body {
    width: 1200px; height: 900px; overflow: hidden;
    background: var(--backdrop);
    font-family: "Work Sans", sans-serif;
    color: var(--white);
  }
  .canvas {
    position: relative; width: 1200px; height: 900px;
    background: radial-gradient(ellipse at 50% 40%, #1f1f1f 0%, var(--backdrop) 70%);
  }
  .card {
    position: absolute; left: 260px; width: 680px; height: 388px;
    background: linear-gradient(160deg, var(--card) 0%, var(--card-edge) 100%);
    border-bottom: 7px solid var(--green);
    box-shadow: 0 18px 40px rgba(0,0,0,.55);
  }
  .card--front { top: 45px; }
  .card--back { top: 467px; }

  .wordmark {
    display: flex; align-items: center; gap: 14px;
    font-weight: 500; color: var(--white); letter-spacing: 1px;
  }
  .wordmark__square { width: 44px; height: 44px; background: var(--green); }
  .card--front .wordmark {
    position: absolute; left: 0; right: 0; top: 150px;
    justify-content: center; font-size: 72px; line-height: 1;
  }
  .card--back .wordmark {
    position: absolute; left: 50px; top: 160px;
    font-size: 54px; line-height: 1;
  }
  .card--back .wordmark__square { width: 34px; height: 34px; }

  .divider {
    position: absolute; left: 340px; top: 62px;
    width: 2px; height: 250px; background: var(--green);
  }
  .contact {
    position: absolute; left: 366px; top: 64px; right: 20px;
  }
  .contact__name { font-size: 28px; font-weight: 600; color: var(--green); line-height: 1.15; }
  .contact__role { font-size: 18px; font-weight: 400; margin-bottom: 14px; }
  .contact__address { font-size: 16px; line-height: 1.35; margin-bottom: 10px; letter-spacing: .3px; }
  .contact__line {
    display: flex; align-items: center; gap: 10px;
    font-size: 16px; line-height: 1.6; letter-spacing: .3px; white-space: nowrap;
  }
  .contact__icon { width: 13px; height: 13px; flex: none; }
</style>
</head>
<body>
<main class="canvas">
  <section class="card card--front" aria-label="Card front">
    <div class="wordmark"><span class="wordmark__square"></span><span>brovix</span></div>
  </section>

  <section class="card card--back" aria-label="Card back">
    <div class="wordmark"><span class="wordmark__square"></span><span>brovix</span></div>
    <div class="divider"></div>
    <div class="contact">
      <p class="contact__name">Halyna Dorosh</p>
      <p class="contact__role">Director of Marketing</p>
      <p class="contact__address">20517 - 87 Ave. Edmonton, AB,<br>Canada. T6K 4N8</p>
      <p class="contact__line">
        <svg class="contact__icon" viewBox="0 0 16 16" aria-hidden="true"><path fill="#8cc63f" d="M3.6 1l2.4 2.8-1.4 1.8c.9 2 2.6 3.8 4.8 4.8l1.8-1.4L14 11.4 12.4 14C6.6 13.6 2.4 9.4 2 3.6z"/></svg>
        780.555.0184
      </p>
      <p class="contact__line">
        <svg class="contact__icon" viewBox="0 0 16 16" aria-hidden="true"><g fill="none" stroke="#8cc63f" stroke-width="1.4"><rect x="4" y="1.5" width="8" height="13" rx="1.5"/><path d="M7 12h2"/></g></svg>
        780.555.0127
      </p>
      <p class="contact__line">
        <svg class="contact__icon" viewBox="0 0 16 16" aria-hidden="true"><rect x="1.5" y="3.5" width="13" height="9" fill="none" stroke="#8cc63f" stroke-width="1.5"/><path d="M1.5 3.5L8 9l6.5-5.5" fill="none" stroke="#8cc63f" stroke-width="1.5"/></svg>
        halya.dorosh@quillmail.example
      </p>
      <p class="contact__line">
        <svg class="contact__icon" viewBox="0 0 16 16" aria-hidden="true"><g fill="none" stroke="#8cc63f" stroke-width="1.3"><circle cx="8" cy="8" r="6.3"/><ellipse cx="8" cy="8" rx="2.8" ry="6.3"/><path d="M1.7 8h12.6M2.7 4.8h10.6M2.7 11.2h10.6"/></g></svg>
        www.brovix.example
      </p>
    </div>
  </section>
</main>
</body>
</html>
```